Business Card Design Project

I need a business card designed from scratch. I have an existing logo that I can upload in Illustrator for modification or redesign.

The Company is called Query Lanterns http://querylanterns.com.au and we provide Search Engine Optimization services to Australian businesses. The current logo signifies an increase in visitors, profits etc...

There are no restrictions as to the redesign - colours, style etc are all open to change.

Cards will be full colour and one sided printed at http://www.cardmoxel.com.au so check their requirements for file format and sizes etc.

I will expect all original files upon completion of project.

Target Market(s)

Any business with a web site looking to improve their search engine rankings

Industry/Entity Type

Business

Requirements
Must have
• I like modern, sleek designs. Clean, not fussy, uncluttered.

```html
<!DOCTYPE html>
<html lang="en">
<head>
<meta charset="utf-8">
<title>Query Lanterns – Business Card</title>
<link href="https://fonts.googleapis.com/css2?family=Open+Sans:wght@600;700;800&display=swap" rel="stylesheet">
<style>
  :root {
    --bg: #e9e9e9;
    --card-front: #000000;
    --card-back: #ffffff;
    --brand-blue: #1a6fb8;
    --brand-yellow: #f2c418;
    --shadow: rgba(0,0,0,0.35);
  }
  html, body {
    margin: 0;
    padding: 0;
    width: 1187px;
    height: 1200px;
    overflow: hidden;
    background: var(--bg);
    font-family: "Open Sans", Arial, sans-serif;
  }
  .canvas { position: relative; width: 1187px; height: 1200px; }
  .card {
    position: absolute;
    left: 221px;
    width: 726px;
    height: 470px;
    box-shadow: 0 6px 18px var(--shadow);
  }
  .card--front { top: 73px; background: var(--card-front); }
  .card--back { top: 643px; background: var(--card-back); }

  .front-name {
    position: absolute;
    left: 0; right: 0;
    top: 200px;
    text-align: center;
    font-weight: 800;
    font-size: 56px;
    color: var(--brand-yellow);
    letter-spacing: -0.5px;
  }

  .brand {
    position: absolute;
    left: 24px;
    top: 318px;
    display: flex;
    align-items: center;
    gap: 12px;
  }
  .brand__dot {
    width: 26px; height: 26px;
    border-radius: 50%;
    background: var(--brand-yellow);
  }
  .brand__name {
    font-weight: 800;
    font-size: 31px;
    color: var(--brand-blue);
    letter-spacing: -0.5px;
  }

  .divider {
    position: absolute;
    left: 320px;
    top: 299px;
    width: 6px;
    height: 123px;
    background: var(--brand-yellow);
  }

  .contact {
    position: absolute;
    left: 370px;
    top: 295px;
  }
  .contact__name {
    margin: 0 0 0 15px;
    font-weight: 700;
    font-size: 20px;
    color: var(--brand-blue);
  }
  .contact__title {
    margin: 0 0 14px 19px;
    font-weight: 700;
    font-size: 16px;
    color: var(--brand-blue);
  }
  .contact__list { list-style: none; margin: 0; padding: 0; }
  .contact__item {
    display: flex;
    align-items: center;
    gap: 9px;
    height: 27px;
    font-weight: 700;
    font-size: 14px;
    color: var(--brand-yellow);
  }
  .contact__icon { width: 22px; height: 22px; fill: var(--brand-blue); }
</style>
</head>
<body>
<div class="canvas">
  <section class="card card--front">
    <div class="front-name">Query Lanterns</div>
  </section>

  <section class="card card--back">
    <div class="brand">
      <span class="brand__dot"></span>
      <span class="brand__name">Query Lanterns</span>
    </div>

    <div class="divider"></div>

    <div class="contact">
      <p class="contact__name">Dale Marsh</p>
      <p class="contact__title">Internet Marketing Consultant</p>
      <ul class="contact__list">
        <li class="contact__item">
          <svg class="contact__icon" viewBox="0 0 24 24" aria-hidden="true">
            <circle cx="12" cy="12" r="10" fill="none" stroke="#1a6fb8" stroke-width="2"/>
            <ellipse cx="12" cy="12" rx="4.5" ry="10" fill="none" stroke="#1a6fb8" stroke-width="1.8"/>
            <line x1="2" y1="12" x2="22" y2="12" stroke="#1a6fb8" stroke-width="1.8"/>
            <line x1="4" y1="7" x2="20" y2="7" stroke="#1a6fb8" stroke-width="1.5"/>
            <line x1="4" y1="17" x2="20" y2="17" stroke="#1a6fb8" stroke-width="1.5"/>
          </svg>
          www.querylanterns.com.au
        </li>
        <li class="contact__item">
          <svg class="contact__icon" viewBox="0 0 24 24" aria-hidden="true">
            <rect x="2" y="5" width="20" height="14" rx="1.5"/>
            <polyline points="3,6 12,13 21,6" fill="none" stroke="#ffffff" stroke-width="1.8"/>
          </svg>
          dale@querylanterns.com.au
        </li>
        <li class="contact__item">
          <svg class="contact__icon" viewBox="0 0 24 24" aria-hidden="true">
            <path d="M3 8c0-2 4-4 9-4s9 2 9 4v2h-5V8H8v2H3z"/>
            <path d="M6 11h12l2 9H4z"/>
            <circle cx="12" cy="15" r="2.5" fill="#ffffff"/>
          </svg>
          1300 555 018
        </li>
      </ul>
    </div>
  </section>
</div>
</body>
</html>
```